Looking for a modern, Professional business card design

We have a simple business card, but are looking for a more modern, professional look. A sample of the basic card is attached as well as the logo. We would also like to add that we offer:
Struggling with your finances?
- Learn to become debt free
- Discover the power of cash
- Control your money instead of it controlling you
Let us help you achieve a new level of financial freedom!
Also, we would like to have a "SPECIAL OFFER!: FREE 30 minute consultation"
Financial Planning

```html
<!DOCTYPE html>
<html lang="en">
<head>
<meta charset="utf-8">
<title>Clearpath Money Coaching – Business Card</title>
<link rel="stylesheet" href="https://fonts.googleapis.com/css2?family=Anton&family=PT+Sans:ital,wght@0,400;0,700;1,700&display=swap">
<style>
  :root {
    --backdrop: #151515;
    --card-white: #ffffff;
    --brand-green: #3f9a3a;
    --brand-green-deep: #2f8a2c;
    --offer-green: #45953f;
    --offer-glow: #6db94a;
    --ink: #1a1a1a;
    --on-green: #ffffff;
  }
  * { margin: 0; padding: 0; box-sizing: border-box; }
  html, body {
    width: 1200px; height: 900px; overflow: hidden;
    background: var(--backdrop);
  }
  .canvas { position: relative; width: 1200px; height: 900px; }

  .card {
    position: absolute; top: 170px;
    width: 347px; height: 561px; overflow: hidden;
  }

  /* Front */
  .card--front {
    left: 259px; background: var(--card-white);
    font-family: "PT Sans", Arial, sans-serif; color: var(--ink);
    text-align: center;
  }
  .brand {
    position: absolute; top: 232px; left: 0; width: 100%;
    top: 62px; display: flex; align-items: center; justify-content: center; gap: 12px;
  }
  .brand__dot {
    width: 30px; height: 30px; border-radius: 50%;
    background: var(--brand-green);
  }
  .brand__name {
    font-weight: 700; font-size: 26px; line-height: 1.05;
    color: var(--brand-green); text-align: left;
  }
  .contact { position: absolute; top: 186px; left: 0; width: 100%; }
  .contact__name { font-size: 19px; color: var(--brand-green); line-height: 22px; }
  .contact__role { font-size: 15px; line-height: 20px; }
  .contact__lines { margin-top: 27px; font-size: 15px; line-height: 20px; }

  .pitch { position: absolute; top: 334px; left: 0; width: 100%; }
  .pitch__heading {
    font-size: 14.5px; font-weight: 700; color: var(--brand-green-deep);
    text-transform: uppercase; line-height: 20px; letter-spacing: 0.2px;
  }
  .pitch__list { list-style: none; font-size: 15px; line-height: 20.5px; }
  .pitch__closing {
    margin-top: 19px; font-size: 15px; font-weight: 700; font-style: italic;
    color: var(--brand-green-deep); line-height: 20.5px;
  }

  /* Back */
  .card--back {
    left: 631px; background: var(--offer-green);
    color: var(--on-green); font-family: "PT Sans", Arial, sans-serif;
  }
  .back__decor {
    position: absolute; left: 0; top: 170px; width: 100%; height: 391px;
    background: radial-gradient(ellipse at 55% 45%, rgba(109,185,74,0.55) 0%, rgba(109,185,74,0.15) 45%, rgba(69,149,63,0) 75%);
  }
  .offer-title {
    position: absolute; top: 54px; left: 52px; width: 252px;
    font-family: "Anton", Impact, sans-serif; text-transform: uppercase;
    line-height: 74px;
  }
  .offer-title__line { display: block; font-size: 78px; }
  .offer-title__line--wide { letter-spacing: 11px; }
  .offer-detail {
    position: absolute; top: 354px; left: 50px; width: 260px;
    font-weight: 700; text-transform: uppercase;
  }
  .offer-detail__big { display: block; font-size: 68px; line-height: 58px; letter-spacing: -0.5px; }
  .offer-detail__small { display: block; font-size: 37.5px; line-height: 50px; letter-spacing: -0.3px; }
</style>
</head>
<body>
<main class="canvas">

  <section class="card card--front" aria-label="Business card front">
    <div class="brand">
      <span class="brand__dot"></span>
      <span class="brand__name">Clearpath<br>Money Coaching</span>
    </div>

    <div class="contact">
      <p class="contact__name">Daniel R. Hayes</p>
      <p class="contact__role">Personal Financial coach</p>
      <p class="contact__lines">(555)010-4821<br>daniel@clearpathmoneyplan.com</p>
    </div>

    <div class="pitch">
      <p class="pitch__heading">Struggling with your finances?</p>
      <ul class="pitch__list">
        <li>Learn to become debt free</li>
        <li>Discover the power of cash</li>
        <li>Control your money<br>instead of it controlling you</li>
      </ul>
      <p class="pitch__closing">Let us help you achieve a new level<br>of financial freedom!</p>
    </div>
  </section>

  <section class="card card--back" aria-label="Business card back">
    <div class="back__decor" role="img" aria-label="Faint large brand mark decoration"></div>
    <h2 class="offer-title">
      <span class="offer-title__line">Special</span>
      <span class="offer-title__line offer-title__line--wide">Offer!</span>
    </h2>
    <p class="offer-detail">
      <span class="offer-detail__big">Free 30</span>
      <span class="offer-detail__big">Minute</span>
      <span class="offer-detail__small">Consultation</span>
    </p>
  </section>

</main>
</body>
</html>
```